Veldmark Supplies Business Card

Professional business card that stand out to our potential customers. Front and back with clean modern design

Industry/Entity Type

Oil and gas

Contact Information for Business Card

Name, address, website , office phone and cell number

Requirements
Must have
• Editable files for each employee

```html
<!DOCTYPE html>
<html lang="en">
<head>
<meta charset="utf-8">
<title>Veldmark Supplies Business Card</title>
<link rel="stylesheet" href="https://fonts.googleapis.com/css2?family=Roboto:wght@400;500;700&display=swap">
<style>
  :root {
    --backdrop: #2b2b2d;
    --card: #1d1d1f;
    --gloss: #5a5a5e;
    --text: #e9e9ea;
    --accent-blue: #1fa8d6;
    --accent-red: #e42b2b;
  }
  * { margin: 0; padding: 0; box-sizing: border-box; }
  html, body {
    width: 1200px; height: 852px; overflow: hidden;
    background: var(--backdrop);
    font-family: "Roboto", Arial, sans-serif;
  }
  .stage {
    width: 1200px; height: 852px;
    display: flex; flex-direction: column;
    align-items: center; justify-content: center; gap: 40px;
  }
  .card {
    position: relative;
    width: 640px; height: 366px;
    background: var(--card);
    border-radius: 20px;
    overflow: hidden;
    box-shadow: 0 10px 24px rgba(0,0,0,.45);
  }
  /* front */
  .card-front {
    display: flex; align-items: center; justify-content: center; gap: 16px;
  }
  .front-mark {
    width: 34px; height: 34px;
    background: var(--gloss);
  }
  .front-name {
    font-size: 38px; font-weight: 700; letter-spacing: 3px;
    text-transform: uppercase; color: var(--gloss);
  }
  /* back */
  .brand-name {
    position: absolute; left: 44px; top: 190px;
    font-size: 30px; font-weight: 700; line-height: 1.1;
    color: var(--accent-red);
  }
  .contact {
    position: absolute; left: 360px; top: 70px;
    color: var(--text);
  }
  .person-name { font-size: 24px; font-weight: 500; color: var(--accent-blue); }
  .person-role { font-size: 15px; margin-top: 4px; }
  .address { font-size: 15px; line-height: 1.4; margin-top: 26px; }
  .channels { list-style: none; margin-top: 6px; font-size: 15px; line-height: 1.45; }
  .channels li { display: flex; align-items: center; gap: 10px; }
  .channel-icon { width: 14px; height: 14px; flex: none; color: var(--accent-red); }
  .edge-band {
    position: absolute; left: 0; right: 0; bottom: 0; height: 8px;
    display: flex;
  }
  .edge-band .band-red { flex: 0 0 62%; background: var(--accent-red); }
  .edge-band .band-blue { flex: 1; background: var(--accent-blue); }
</style>
</head>
<body>
<main class="stage">
  <section class="card card-front" aria-label="Card front">
    <span class="front-mark"></span>
    <span class="front-name">Veldmark Supplies</span>
  </section>

  <section class="card card-back" aria-label="Card back">
    <div class="brand-name">Veldmark<br>Supplies</div>
    <div class="contact">
      <div class="person-name">John Doe Smith</div>
      <div class="person-role">Managing Director</div>
      <div class="address">420 Larkmoor Ave Suite 7<br>Brenford, Tx 70412</div>
      <ul class="channels">
        <li>
          <svg class="channel-icon" viewBox="0 0 16 16" aria-hidden="true"><path fill="currentColor" d="M3 1h3l1.5 4-2 1.2a9 9 0 0 0 4.3 4.3L11 8.5l4 1.5v3a2 2 0 0 1-2 2A12 12 0 0 1 1 3a2 2 0 0 1 2-2z"/></svg>
          (555)010-0624
        </li>
        <li>
          <svg class="channel-icon" viewBox="0 0 16 16" aria-hidden="true"><path d="M1 3h14v10H1z M2 4l6 5 6-5" fill="none" stroke="currentColor" stroke-width="1.6"/></svg>
          sales@veldmarksupplies.com
        </li>
        <li>
          <svg class="channel-icon" viewBox="0 0 16 16" aria-hidden="true"><g fill="none" stroke="currentColor" stroke-width="1.4"><circle cx="8" cy="8" r="6.5"/><ellipse cx="8" cy="8" rx="2.8" ry="6.5"/><path d="M1.5 8h13"/></g></svg>
          www.veldmarksupplies.com
        </li>
      </ul>
    </div>
    <div class="edge-band"><span class="band-red"></span><span class="band-blue"></span></div>
  </section>
</main>
</body>
</html>
```